Business Card - Tidal Lanes

Need Business Card design for company named Tidal Lanes. Software development focused mainly on Brindle Orvix & Zelt Apps. I've attached our logo with both a black and white background. Please add trademark symbol to logo when using.

```html
<!DOCTYPE html>
<html lang="en">
<head>
<meta charset="utf-8">
<title>Tidal Lanes – Business Card</title>
<link rel="stylesheet" href="https://fonts.googleapis.com/css2?family=Open+Sans:wght@400;600;700&display=swap">
<style>
  :root {
    --page: #e9e6e1;
    --card-black: #050505;
    --accent-red: #d8191c;
    --accent-orange: #f7922e;
    --accent-yellow: #fcc10f;
    --name-yellow: #f5b512;
    --ink-white: #ffffff;
    --ink-grey: #c9c9c9;
    --ink-dark: #3a2414;
  }
  * { box-sizing: border-box; margin: 0; padding: 0; }
  html, body { width: 1200px; height: 720px; overflow: hidden; }
  body {
    background: var(--page);
    font-family: "Open Sans", Arial, sans-serif;
    position: relative;
  }
  .card {
    position: absolute;
    top: 205px;
    width: 540px;
    height: 310px;
    border-radius: 4px;
    overflow: hidden;
    background: var(--card-black);
    box-shadow: 0 6px 18px rgba(0,0,0,.18);
  }
  .card--front { left: 40px; }
  .card--back { left: 620px; }
  .card-art { position: absolute; inset: 0; width: 100%; height: 100%; }

  .contact-name {
    position: absolute; right: 112px; top: 22px;
    color: var(--name-yellow); font-weight: 700; font-size: 17px; text-align: right;
  }
  .contact-title {
    position: absolute; right: 112px; top: 44px;
    color: var(--ink-white); font-size: 12px; text-align: right;
  }
  .brand {
    position: absolute; left: 38px; top: 108px;
    display: flex; align-items: center; gap: 10px;
  }
  .brand-dot {
    width: 22px; height: 22px; border-radius: 50%; background: var(--accent-orange);
  }
  .brand-name {
    color: var(--ink-white); font-weight: 700; font-size: 26px; letter-spacing: -0.5px;
  }
  .brand-name sup { font-size: 10px; vertical-align: top; position: relative; top: 2px; }
  .address {
    position: absolute; left: 38px; bottom: 30px;
    color: var(--ink-white); font-size: 13px; line-height: 1.55;
  }
  .phones {
    position: absolute; right: 36px; top: 160px;
    list-style: none; color: var(--ink-dark); font-size: 14px; line-height: 1.7;
  }
  .phones li { display: flex; align-items: center; gap: 7px; }
  .phones svg { width: 12px; height: 12px; fill: var(--ink-dark); }

  .back-brand {
    position: absolute; left: 0; right: 0; top: 112px;
    text-align: center; color: var(--ink-white);
    font-weight: 700; font-size: 58px; letter-spacing: -1.5px;
  }
  .back-brand sup { font-size: 16px; vertical-align: top; position: relative; top: 6px; }
  .web {
    position: absolute; right: 130px; top: 200px;
    color: var(--ink-grey); font-size: 13px; letter-spacing: .5px;
  }
</style>
</head>
<body>
  <section class="card card--front" aria-label="Card front">
    <svg class="card-art" viewBox="0 0 540 310" preserveAspectRatio="none" aria-hidden="true">
      <defs>
        <linearGradient id="warm" x1="0" y1="1" x2="1" y2="0">
          <stop offset="0.3" stop-color="#fcc10f"/>
          <stop offset="0.75" stop-color="#f7922e"/>
        </linearGradient>
      </defs>
      <rect width="540" height="310" fill="url(#warm)"/>
      <path d="M0 0 H505 C480 110 400 240 290 310 H0 Z" fill="#d8191c"/>
      <path d="M0 0 H462 C440 120 360 250 245 310 H0 Z" fill="#050505"/>
    </svg>
    <p class="contact-name">Your Name</p>
    <p class="contact-title">Title</p>
    <div class="brand">
      <span class="brand-dot"></span>
      <span class="brand-name">Tidal Lanes<sup>™</sup></span>
    </div>
    <address class="address">2250 Seabright Ave<br>Marlow, FL 33091</address>
    <ul class="phones">
      <li><svg viewBox="0 0 12 12"><rect x="3" y="0" width="6" height="12" rx="1.2"/></svg>555-014-2200</li>
      <li><svg viewBox="0 0 12 12"><path d="M1 5 Q6 1 11 5 L10 7 L8 6 L8 5 Q6 4 4 5 L4 6 L2 7 Z M3 8 H9 V11 H3 Z"/></svg>555-019-4831</li>
    </ul>
  </section>

  <section class="card card--back" aria-label="Card back">
    <p class="back-brand">Tidal Lanes<sup>™</sup></p>
    <p class="web">www.tidallanes.com</p>
  </section>
</body>
</html>
```